VELTAR WEBSITE

need to create a new website for VELTAR ltd
the company deals with all aspects of safety products & safety wear
we need a simple website to show
ideas can be taken from following website whose products we shall distribute in kenya
www.kwr.co.uk
www.dorvik.eu
www.brimtoolsupplyco.com
www.gardvalewerks.co.za

we need following tabs
1) home - basic company information
2) products - broken down to following categories ie gloves, head protection, ear protection, mouth protection, foot protection
3) contacts

the company profile is a reputable company dealing with all aspects of safety, HSE (health and safety equipment), and PPE (personal protective equipment)

the website should have the dorvik logo for which we are an authorized distributor.
the dorvi industrial range writeup can be picked from their website
Updates

Dear Designers, i shall be able to choose a final design in 2 weeks, sorry i have not been able to finalise this due to a personal reason

Target Market(s)

the buyers are all types of industry who care for their employees safety

Industry/Entity Type

Industrial

Requirements
Must have
• clean look, fresh look, user freindly
Nice to have
• clear images, quick links etc

```html
<!DOCTYPE html>
<html lang="en">
<head>
<meta charset="utf-8">
<title>VELTAR – Specialized Protective &amp; Industrial Products</title>
<link href="https://fonts.googleapis.com/css2?family=Open+Sans:wght@300;400;600;700&family=PT+Serif:ital@1&display=swap" rel="stylesheet">
<style>
:root{
  --navy:#12303d;
  --orange:#f5a51c;
  --orange-text:#f7a823;
  --page:#eceff0;
  --panel:#d9dee1;
  --text:#2b3438;
  --muted:#7c8489;
  --footer:#141414;
  --footer-text:#c9c9c9;
  --white:#ffffff;
}
*{box-sizing:border-box;margin:0;padding:0}
html,body{width:911px;height:1200px;overflow:hidden}
body{position:relative;background:var(--page);font-family:"Open Sans",Arial,sans-serif;color:var(--text)}
.abs{position:absolute}
.top-rule{left:0;top:0;width:911px;height:3px;background:var(--navy)}
.header{left:0;top:3px;width:911px;height:128px;background:linear-gradient(#f4f5f5,#fafafa 60%,#f0f1f1)}
.brand{left:86px;top:48px;display:flex;align-items:center;gap:8px}
.brand-mark{width:22px;height:22px;background:var(--orange)}
.brand-name{font-weight:700;font-size:30px;color:var(--navy);letter-spacing:1px}
.call{right:85px;top:31px;text-align:right}
.call-note{font-size:11px;color:var(--text);display:flex;align-items:center;gap:3px;justify-content:flex-end}
.call-number{font-size:15px;font-weight:600;color:var(--navy);line-height:18px}
.search{left:666px;top:71px;width:160px;height:22px;background:var(--white);border:1px solid #e0e3e4;border-radius:2px}
.search span{position:absolute;left:7px;top:4px;font-size:9px;color:#c5c9cb}
.search svg{position:absolute;right:5px;top:3px}
.hero{left:0;top:131px;width:911px;height:322px;background:linear-gradient(100deg,#5a6670 0%,#7c6a55 30%,#b07a3c 55%,#6d5a48 80%,#8a7a68 100%)}
.hero-curve{left:0;top:420px}
.nav{left:82px;top:132px;width:744px;height:30px;background:var(--navy);display:flex;align-items:center;justify-content:space-between;padding:0 14px 0 15px}
.nav a{color:var(--white);font-size:10.2px;text-decoration:none;white-space:nowrap}
.nav a.active{background:var(--orange);color:var(--navy);font-weight:700;padding:5px 7px;font-size:10px}
.hero-caption{left:518px;top:233px;width:309px;height:136px;background:rgba(30,24,20,.78);padding:12px 14px}
.hero-caption h1{font-weight:300;font-size:25px;color:var(--white);line-height:30px;letter-spacing:-.3px;white-space:nowrap}
.hero-caption h1 b{font-weight:600;color:var(--orange-text)}
.hero-caption p{font-size:10.1px;color:var(--white);line-height:15.3px;margin-top:3px}
.section-title{left:83px;top:469px;font-size:15px;font-weight:600;color:var(--navy)}
.title-rule{left:177px;top:474px;width:370px;height:8px;background:repeating-linear-gradient(135deg,#d0d5d8 0 1px,transparent 1px 3px)}
.pager{left:556px;top:474px}
.service-name{left:83px;top:499px;font-size:11px;color:var(--text)}
.service-sub{left:83px;top:515px;font-size:8.5px;color:var(--muted)}
.gallery-btn{left:83px;top:538px;width:155px;height:22px;background:var(--orange);color:var(--white);font-size:8.5px;padding:5px 9px;white-space:nowrap}
.icon{width:42px;text-align:center}
.icon-circle{width:42px;height:42px;border-radius:50%;background:linear-gradient(#e6eaec,#b9c3c7);border:2px solid #fff;display:flex;align-items:center;justify-content:center}
.icon-label{font-size:9px;margin-top:10px;color:var(--text)}
.service-photo{left:266px;top:498px;width:311px;height:159px;background:var(--white);padding:3px;box-shadow:0 0 2px rgba(0,0,0,.2)}
.service-photo div{width:100%;height:100%;background:linear-gradient(120deg,#4a3a2c,#7b6a58 45%,#3b3530 70%,#8b8680)}
.service-copy{left:88px;top:674px;width:490px;font-family:Arial,sans-serif;font-size:9.3px;line-height:14px;color:var(--muted)}
.divider{left:88px;top:742px;width:486px;height:1px;background:#dfe3e5}
.partner{left:598px;top:466px;width:227px;height:213px;background:var(--panel)}
.partner-badge{left:13px;top:14px;width:200px;height:53px;background:#f1f2f2;border:4px solid var(--white);display:flex;align-items:center;justify-content:center}
.partner-badge span{font-size:30px;font-weight:700;color:#1a5f97}
.partner-copy{left:13px;top:84px;width:205px;font-family:Arial,sans-serif;font-size:9.2px;line-height:14.3px;color:#8a9296}
.view-more{left:14px;top:178px;font-family:"PT Serif",Georgia,serif;font-style:italic;font-size:9.5px;color:var(--navy)}
.carousel{left:82px;top:770px;width:743px;height:202px;background:var(--panel)}
.card{top:22px;width:160px}
.card-photo{width:160px;height:94px;background:var(--white);padding:3px}
.card-photo div{width:100%;height:100%}
.card h3{font-size:11px;font-weight:400;margin:9px 0 0 4px;color:var(--text)}
.card p{font-size:8.6px;line-height:11.5px;margin:6px 0 0 4px;color:var(--text)}
.arrow{width:21px;height:21px;background:var(--navy);display:flex;align-items:center;justify-content:center}
.footer{left:0;top:1012px;width:911px;height:188px;background:var(--footer);border-top:2px solid #3a3a3a}
.up{left:435px;top:997px;width:38px;height:38px;border-radius:50%;background:#555;display:flex;align-items:center;justify-content:center}
.member-title{left:100px;top:1052px;font-size:13px;font-weight:300;color:#a9a9a9;display:flex;align-items:center;gap:7px}
.member-copy{left:100px;top:1081px;width:260px;font-size:9px;line-height:17px;color:var(--footer-text)}
.member-copy b{color:var(--orange-text);font-weight:400}
.member-btn{left:100px;top:1158px;width:178px;height:23px;background:var(--orange);color:var(--white);font-size:9px;font-weight:600;line-height:23px;padding:0 10px;white-space:nowrap}
.footer-heading{font-size:12.5px;font-weight:600;color:var(--white)}
.links{font-size:9px;line-height:16.8px;color:var(--footer-text);list-style:none}
.contact{font-size:9px;line-height:13.6px;color:var(--footer-text)}
</style>
</head>
<body>
<div class="abs top-rule"></div>
<header class="abs header"></header>
<div class="abs brand"><span class="brand-mark"></span><span class="brand-name">VELTAR</span></div>
<div class="abs call">
  <div class="call-note"><svg width="10" height="10" viewBox="0 0 24 24"><path fill="#12303d" d="M6.6 10.8a15 15 0 006.6 6.6l2.2-2.2c.3-.3.7-.4 1-.2 1.1.4 2.3.6 3.6.6.6 0 1 .4 1 1V20c0 .6-.4 1-1 1A17 17 0 013 4c0-.6.4-1 1-1h3.5c.6 0 1 .4 1 1 0 1.3.2 2.5.6 3.6.1.3 0 .7-.2 1z"/></svg>You call, we're there</div>
  <div class="call-number">(800) 555-0142</div>
</div>
<div class="abs search"><span>Search</span><svg width="15" height="15" viewBox="0 0 24 24"><circle cx="10" cy="10" r="7" fill="none" stroke="#12303d" stroke-width="3"/><path d="M15 15l6 6" stroke="#12303d" stroke-width="3.5" stroke-linecap="round"/></svg></div>

<div class="abs hero" role="img" aria-label="Worker wearing ear defenders and goggles grinding metal with sparks flying"></div>
<svg class="abs hero-curve" width="911" height="40" viewBox="0 0 911 40"><path d="M0 40 L0 24 Q300 -6 600 14 T911 26 L911 40 Z" fill="#eceff0"/></svg>
<nav class="abs nav">
  <a class="active" href="#">HOME</a><a href="#">Head Protection</a><a href="#">Foot Protection</a><a href="#">Ear Protection</a><a href="#">Health and Safety Equipment</a><a href="#">Mouth Protection</a><a href="#">Contact Us</a>
</nav>
<div class="abs hero-caption">
  <h1><b>Ear Protection</b> for you</h1>
  <p>It is a long established fact that a reader will be distracted by the readable content of a page when looking at its layout. The point of using Lorem Ipsum is that it has a more-or-less normal distribution of letters, as opposed to using 'Content here, content here',</p>
</div>

<h2 class="abs section-title">Our Services</h2>
<div class="abs title-rule"></div>
<svg class="abs pager" width="14" height="8" viewBox="0 0 14 8"><path d="M4 0L0 4l4 4z M10 0l4 4-4 4z" fill="#9aa3a7"/></svg>
<div class="abs service-name">Persoan Protection</div>
<div class="abs service-sub">Lorem Ipsum is simply dummy text</div>
<div class="abs gallery-btn">The Equipment&nbsp; show on Gallery</div>

<div class="abs icon" style="left:87px;top:575px"><div class="icon-circle"><svg width="22" height="22" viewBox="0 0 24 24"><path d="M9 20c2 1 4 0 5-2s3-3 3-7a5 5 0 00-10 0" fill="none" stroke="#12303d" stroke-width="2"/><path d="M2 11h6l-2-2m2 2l-2 2" fill="none" stroke="#12303d" stroke-width="2"/></svg></div><div class="icon-label">EAR</div></div>
<div class="abs icon" style="left:139px;top:575px"><div class="icon-circle"><svg width="22" height="22" viewBox="0 0 24 24"><path d="M7 21v-4a7 7 0 1110-6l2 3h-2v3h-3v4" fill="none" stroke="#12303d" stroke-width="2"/></svg></div><div class="icon-label">HEAD</div></div>
<div class="abs icon" style="left:191px;top:575px"><div class="icon-circle"><svg width="22" height="22" viewBox="0 0 24 24"><path d="M7 21v-8L5 8l2-1 2 4V4h2v7V3h2v8V4h2v8l2-4h2l-3 9v5z" fill="#12303d"/></svg></div><div class="icon-label">GLOVES</div></div>

<div class="abs service-photo"><div role="img" aria-label="Two workers in protective gear cutting timber at a workshop saw"></div></div>
<p class="abs service-copy">Aliquam erat volutpat. Duis blandit augue ac orci laoreet eget condimentum magna venenatis. Maecenas eget augue in nisl malesuada mollis. Vivamus eget bibendum dolor. Nulla vel varius mi. In hac habitasse platea dictumst. Duis</p>
<div class="abs divider"></div>

<aside class="abs partner">
  <div class="abs partner-badge"><span>Dorvik</span></div>
  <p class="abs partner-copy">Duis ac nisi et libero suscipit lobortis ac at velit. Cum sociis natoque penatibus et magnis dis parturient montes, nascetur ridiculus mus. Suspendisse ac nibh id magna adipiscing venenatis ac eu eros. Morbi euismod auctor ipsum, eget mollis eros</p>
  <div class="abs view-more">View more →</div>
</aside>

<section class="abs carousel">
  <div class="abs card" style="left:26px"><div class="card-photo"><div role="img" aria-label="Worker in a blue hard hat and safety glasses" style="background:linear-gradient(135deg,#2f6fb5,#8aa4bc 55%,#cfd6dc)"></div></div><h3>Head Protection</h3><p>Lorem Ipsum is simply dummy text of the printing and typesetting indus-try. Lorem</p></div>
  <div class="abs card" style="left:202px"><div class="card-photo"><div role="img" aria-label="Hands pulling on blue nitrile gloves" style="background:linear-gradient(135deg,#d9c6ae,#4a9fd6 50%,#c8b49a)"></div></div><h3>Gloves</h3><p>Lorem Ipsum is simply dummy text of the printing and typesetting indus-try. Lorem</p></div>
  <div class="abs card" style="left:376px"><div class="card-photo"><div role="img" aria-label="Pair of leather safety boots" style="background:linear-gradient(#e39a3c,#5a3f2c 60%,#3b2a20)"></div></div><h3>Foot Protection</h3><p>Lorem Ipsum is simply dummy text of the printing and typesetting indus-try. Lorem</p></div>
  <div class="abs card" style="left:554px"><div class="card-photo"><div role="img" aria-label="Clear mouth guards on a wooden surface" style="background:linear-gradient(135deg,#b8702f,#d69a55 50%,#9b5a25)"></div></div><h3>Mouth Protection</h3><p>Lorem Ipsum is simply dummy text of the printing and typesetting indus-try. Lorem</p></div>
</section>
<div class="abs arrow" style="left:78px;top:878px"><svg width="10" height="10" viewBox="0 0 10 10"><path d="M7 1L3 5l4 4" fill="none" stroke="#fff" stroke-width="2"/></svg></div>
<div class="abs arrow" style="left:809px;top:874px"><svg width="10" height="10" viewBox="0 0 10 10"><path d="M3 1l4 4-4 4" fill="none" stroke="#fff" stroke-width="2"/></svg></div>

<footer class="abs footer"></footer>
<div class="abs up"><svg width="14" height="10" viewBox="0 0 14 10"><path d="M1 8l6-6 6 6" fill="none" stroke="#fff" stroke-width="2.5"/></svg></div>
<div class="abs member-title"><svg width="16" height="16" viewBox="0 0 16 16"><path d="M8 0v16M0 8h16M2.5 2.5l11 11M13.5 2.5l-11 11" stroke="#bbb" stroke-width="1.3"/></svg>Become a Member!</div>
<p class="abs member-copy"><b>Lorem Ipsum</b> is simply dummy text of the printing and type-setting industry. Lorem Ipsum has been the industry's standard dummy text ever since the 1500s, when an unknown printer took a galley of type and scrambled</p>
<div class="abs member-btn">Be contacted by a selvra consultant</div>

<h4 class="abs footer-heading" style="left:457px;top:1053px">POPULAR</h4>
<ul class="abs links" style="left:455px;top:1082px">
  <li>Equipment FAQs</li><li>Common Venting of Gas Appliances</li><li>Becoming a Member</li><li>Education / CECs</li><li>Affiliate Directory</li>
</ul>

<h4 class="abs footer-heading" style="left:658px;top:1053px">CONTACT US</h4>
<div class="abs contact" style="left:658px;top:1079px">240 Harlow Lane&nbsp; Suite 12<br>Kestrel Bay 10482<br>Hours: M-F, 8:00am - 5:00pm</div>
<div class="abs contact" style="left:658px;top:1127px">Phone: (800) 555-0177 or<br>(916) 555-0123<br>Fax: (916) 555-0168</div>
</body>
</html>
```